Business Card Design For A Renovation Contractor Company

We need a business card for a new company based in Singapore, our company name is "RB Tolvane". We are a renovation contractor that builds designs into reality. We build more of F&B restaurants, retail stores and commercial offices. We work very closely with designers. The final design should communicate to our client that we are a company that you can trust, that will plan and complete your project without giving you a headache. I like my client to remember my company as "RB". The beauty of SIMPLE is important.

Industry/Entity Type

Contractor

Requirements
Nice to have
• Black or Red base

```html
<!DOCTYPE html>
<html lang="en">
<head>
<meta charset="utf-8">
<title>RB Tolvane — Business Cards</title>
<link href="https://fonts.googleapis.com/css2?family=Didact+Gothic&family=Source+Sans+3:wght@400;600&display=swap" rel="stylesheet">
<style>
  :root {
    --backdrop: #e4e7e9;
    --card-white: #ffffff;
    --brand-red: #e2262c;
    --deep-red: #b3161c;
    --card-black: #262324;
    --ink: #2f2c2d;
    --ink-soft: #6a6667;
    --paper-text: #ffffff;
    --muted-light: #d9d6d6;
  }
  * { margin: 0; padding: 0; box-sizing: border-box; }
  html, body {
    width: 1200px; height: 505px; overflow: hidden;
    background: var(--backdrop);
  }
  .canvas { position: relative; width: 1200px; height: 505px; }
  .card {
    position: absolute; top: 129px;
    width: 322px; height: 171px; overflow: hidden;
  }
  .card--contact { left: 77px; background: var(--card-white); }
  .card--red { left: 439px; background: var(--brand-red); }
  .card--black { left: 801px; background: var(--card-black); }

  .card__shape { position: absolute; inset: 0; }

  .brand {
    position: absolute; display: flex; flex-direction: column; align-items: center;
    font-family: "Didact Gothic", sans-serif;
  }
  .brand__mark { border-radius: 50%; border: 2.5px solid currentColor; }
  .brand__name { line-height: 1; white-space: nowrap; }
  .brand__tagline { line-height: 1; white-space: nowrap; }
  .brand__web {
    font-family: "Source Sans 3", sans-serif; font-weight: 600; line-height: 1;
  }

  .card--contact .brand { left: 8px; width: 126px; top: 46px; color: var(--ink); }
  .card--contact .brand__mark { width: 30px; height: 30px; border-color: var(--deep-red); }
  .card--contact .brand__name { font-size: 19px; margin-top: 6px; }
  .card--contact .brand__tagline { font-size: 7px; margin-top: 3px; color: var(--ink-soft); }

  .card--red .brand, .card--black .brand { left: 0; right: 0; top: 42px; }
  .card--red .brand { color: var(--deep-red); }
  .card--black .brand { color: var(--muted-light); }
  .card--red .brand__mark, .card--black .brand__mark { width: 40px; height: 40px; }
  .card--red .brand__name, .card--black .brand__name { font-size: 25px; margin-top: 8px; }
  .card--red .brand__tagline, .card--black .brand__tagline { font-size: 8.5px; margin-top: 3px; }
  .card--red .brand__web, .card--black .brand__web { font-size: 9px; margin-top: 6px; }
  .card--black .brand__web { color: var(--paper-text); }

  .person {
    position: absolute; left: 201px; top: 36px; color: var(--paper-text);
    font-family: "Source Sans 3", sans-serif;
  }
  .person__name { font-size: 12.5px; line-height: 1.1; }
  .person__role { font-size: 8.5px; margin-top: 3px; }

  .contact-list {
    position: absolute; left: 199px; top: 97px; list-style: none;
    font-family: "Source Sans 3", sans-serif; font-size: 9.5px; color: var(--paper-text);
  }
  .contact-list li { display: flex; align-items: center; gap: 5px; height: 14px; }
  .contact-list svg { width: 7px; height: 7px; fill: var(--paper-text); flex: none; }
</style>
</head>
<body>
<main class="canvas">

  <section class="card card--contact">
    <svg class="card__shape" viewBox="0 0 322 171" preserveAspectRatio="none" aria-hidden="true">
      <path d="M138 0 Q198 86 120 171 L322 171 L322 0 Z" fill="var(--card-black)"/>
      <path d="M150 0 Q207 88 134 171 L322 171 L322 0 Z" fill="var(--brand-red)"/>
    </svg>
    <div class="brand">
      <span class="brand__mark"></span>
      <span class="brand__name">RB Tolvane</span>
      <span class="brand__tagline">built to plan, built to last</span>
    </div>
    <div class="person">
      <p class="person__name">Mara Quell</p>
      <p class="person__role">Managing Director</p>
    </div>
    <ul class="contact-list">
      <li><svg viewBox="0 0 10 10"><path d="M2 0.5 L4 2.8 L3 4 Q4.5 6 6 7 L7.2 6 L9.5 8 L8 9.6 Q3.5 9 0.4 2 Z"/></svg>614.280.3957</li>
      <li><svg viewBox="0 0 10 10"><rect x="2.5" y="0.5" width="5" height="3"/><rect x="0.5" y="3.5" width="9" height="4" rx="1"/><rect x="2.5" y="6.5" width="5" height="3"/></svg>614.280.3958</li>
      <li><svg viewBox="0 0 10 10"><path d="M0.5 2 H9.5 V8.5 H0.5 Z M0.5 2 L5 5.5 L9.5 2" stroke="var(--brand-red)" stroke-width="0.8"/></svg>info@rbtolvane.com</li>
      <li><svg viewBox="0 0 10 10"><circle cx="5" cy="5" r="4.5"/></svg>www.rbtolvane.com</li>
    </ul>
  </section>

  <section class="card card--red">
    <div class="brand">
      <span class="brand__mark"></span>
      <span class="brand__name">RB Tolvane</span>
      <span class="brand__tagline">built to plan, built to last</span>
      <span class="brand__web">www.rbtolvane.com</span>
    </div>
  </section>

  <section class="card card--black">
    <div class="brand">
      <span class="brand__mark"></span>
      <span class="brand__name">RB Tolvane</span>
      <span class="brand__tagline">built to plan, built to last</span>
      <span class="brand__web">www.rbtolvane.com</span>
    </div>
  </section>

</main>
</body>
</html>
```